Kelvara Pane Works Business Card

We need a business card design that is suitable for a Glazing Business. We Specialize in Repairing broken windows and doors and are a 24hr on call service. We manufacture Shower screens, Fly screens, Wardrobe doors, Security doors and grilles + mirrors. We stock a variety of mesh including Standard mesh, Pet resistant mesh, Tressmet & Clearweft. We would like to use a combination of Light Blue, Dark Blue, Black & White with perhaps a picture of glass breaking.

Industry/Entity Type

Business

Contact Information for Business Card

Narooma Glass Service60B Glasshouse Rocks RdNarooma NSW 2546PH / FAX - 02 44765210MOB - 0419682350 Andrewemail - kelvarapane@fenmail.example

Font styles to use
Serif

Colors
34a7d8
0255a3
ffffff

Requirements
Must have
• logo with picture of broken or cracked glass

```html
<!DOCTYPE html>
<html lang="en">
<head>
<meta charset="utf-8">
<title>Kelvara Pane Works – Business Card</title>
<link href="https://fonts.googleapis.com/css2?family=Open+Sans:wght@400;600;700&display=swap" rel="stylesheet">
<style>
  :root {
    --page-bg: #e9ebee;
    --card-dark: #1c1d20;
    --card-dark-edge: #141517;
    --blue-light: #34a7d8;
    --blue-sky: #5cc3e3;
    --blue-deep: #3d7fc4;
    --brand-dark: #0255a3;
    --white: #ffffff;
    --text-soft: #e6e8ea;
    --divider: #4a4d52;
  }
  * { margin: 0; padding: 0; box-sizing: border-box; }
  html, body {
    width: 1200px; height: 844px; overflow: hidden;
    background: var(--page-bg);
    font-family: "Open Sans", Arial, sans-serif;
  }
  .stage {
    position: relative; width: 1200px; height: 844px;
    display: flex; align-items: center; justify-content: center; gap: 48px;
  }
  .card {
    width: 520px; height: 318px; position: relative;
    box-shadow: 0 10px 28px rgba(0,0,0,.22);
  }
  /* Back: contact side */
  .card--contact {
    background: radial-gradient(ellipse at 40% 40%, #26272b, var(--card-dark-edge));
    color: var(--text-soft);
  }
  .brand-mark {
    position: absolute; left: 40px; top: 132px;
    color: var(--blue-light); font-weight: 700;
    font-size: 27px; line-height: 1.12; letter-spacing: 1px;
    text-transform: uppercase;
  }
  .divider {
    position: absolute; left: 262px; top: 62px; width: 1px; height: 196px;
    background: var(--divider);
  }
  .contact {
    position: absolute; left: 282px; top: 58px; font-size: 13.5px; line-height: 1.5;
  }
  .contact__name {
    color: var(--blue-light); font-weight: 600; font-size: 17px; margin-bottom: 6px;
  }
  .contact__address { margin-bottom: 20px; }
  .contact__list { list-style: none; }
  .contact__list li { display: flex; align-items: center; gap: 8px; line-height: 1.6; }
  .contact__list svg { width: 12px; height: 12px; flex: none; fill: var(--blue-light); }

  /* Front: services side */
  .card--services {
    background: linear-gradient(160deg, var(--blue-sky) 0%, var(--blue-light) 40%, var(--blue-deep) 100%);
    color: var(--white);
    text-align: center;
  }
  .card--services .brand-mark {
    position: absolute; left: 0; right: 0; top: 92px;
    color: var(--white); font-size: 36px; letter-spacing: 2px;
  }
  .services {
    position: absolute; left: 0; right: 0; top: 206px;
    font-size: 13.5px; line-height: 1.6;
  }
  .services span { white-space: nowrap; }
  .services span::before {
    content: ""; display: inline-block; width: 8px; height: 8px; border-radius: 50%;
    background: var(--white); margin: 0 5px 1px 8px; vertical-align: middle;
  }
</style>
</head>
<body>
<main class="stage">
  <section class="card card--contact" aria-label="Contact side">
    <div class="brand-mark">Kelvara<br>Pane Works</div>
    <div class="divider"></div>
    <div class="contact">
      <p class="contact__name">Malcolm</p>
      <p class="contact__address">17C Tindale Ridge Rd<br>Tindale NSW 2631</p>
      <ul class="contact__list">
        <li><svg viewBox="0 0 24 24"><path d="M6.6 10.8a15 15 0 0 0 6.6 6.6l2.2-2.2c.3-.3.7-.4 1-.2 1.1.4 2.3.6 3.6.6.6 0 1 .4 1 1V20c0 .6-.4 1-1 1A17 17 0 0 1 3 4c0-.6.4-1 1-1h3.5c.6 0 1 .4 1 1 0 1.3.2 2.5.6 3.6.1.3 0 .7-.2 1z"/></svg>02 48931067</li>
        <li><svg viewBox="0 0 24 24"><path d="M6 2h10v5H6zM4 8h16a2 2 0 0 1 2 2v8h-4v4H6v-4H2v-8a2 2 0 0 1 2-2zm4 9v3h8v-3z"/></svg>02 48931067</li>
        <li><svg viewBox="0 0 24 24"><path d="M7 1h10a2 2 0 0 1 2 2v18a2 2 0 0 1-2 2H7a2 2 0 0 1-2-2V3a2 2 0 0 1 2-2zm0 3v15h10V4z"/></svg>0419682350</li>
        <li><svg viewBox="0 0 24 24"><path d="M2 4h20v16H2zm2 2v.5l8 5 8-5V6z"/></svg>kelvarapane@fenmail.example</li>
      </ul>
    </div>
  </section>

  <section class="card card--services" aria-label="Services side">
    <div class="brand-mark">Kelvara Pane Works</div>
    <p class="services">
      <span>Shower screens</span> <span>Fly screens</span> <span>Wardrobe doors</span><br>
      <span>Security doors</span> <span>Grilles + mirrors</span>
    </p>
  </section>
</main>
</body>
</html>
```